RW Holloway LLC Business Card - Civil Engineering & Consulting Firm

We need a Business Card that is elegant, and masculine.  It is our Professional Civil Engineering & Consulting Company located in San Antonio TX (Not s construction or builder firm- no gears & no tool images please). We provide civil engineering services including  commercial site plans, grading and drainage plans, utility plans, hydraulics and hydrology, land planning, utility coordination, and other general civil engineering services related to commercial and residential development.
We have 2 existing Logos. We would like to convey reliability, strength, trustworthiness and attention to detail.  Blues and orange tones as per logo We are OK with the use of a darker blue in the mix.  We have 2 logo versions - Full Company Name Logo to go on the back of card, & Small Icon Logo for the front w/ personal Info.

Target Market(s)
Architects, Real Estate Developers, Other Strctural Engineers, Surveyers, General Contractors
Industry/Entity Type
Professional Civil Engineering
Contact Information for Business Card
Name, Position, Address, Cell & Office #, email, and company website
Font styles to use
Other font styles liked:
- Avian
Requirements
Should not have
- No Tools, No Gears, no Cranes, or Construction Equipment.

```html
<!DOCTYPE html>
<html lang="en">
<head>
<meta charset="utf-8">
<title>RW Holloway LLC – Business Card</title>
<link href="https://fonts.googleapis.com/css2?family=Josefin+Sans:wght@400;700&family=Questrial&display=swap" rel="stylesheet">
<style>
  :root {
    --backdrop: #2a2b2e;
    --navy: #0f2748;
    --orange: #f0892a;
    --sky: #7fb0e0;
    --white: #ffffff;
  }
  * { box-sizing: border-box; margin: 0; padding: 0; }
  html, body { width: 1200px; height: 874px; overflow: hidden; }
  body {
    background: var(--backdrop);
    position: relative;
    font-family: "Questrial", sans-serif;
  }
  .card {
    position: absolute;
    left: 290px;
    width: 620px;
    height: 355px;
    background: var(--navy);
    overflow: hidden;
    box-shadow: 0 10px 24px rgba(0,0,0,.45);
  }
  .card--back { top: 48px; }
  .card--front { top: 470px; }

  /* back: company name */
  .brand {
    position: absolute;
    left: 0; right: 0; top: 140px;
    text-align: center;
    font-family: "Josefin Sans", sans-serif;
    font-weight: 400;
    font-size: 50px;
    letter-spacing: 6px;
    color: var(--sky);
  }

  /* front: person */
  .person {
    position: absolute;
    right: 364px; top: 150px;
    text-align: right;
  }
  .person__name {
    font-family: "Josefin Sans", sans-serif;
    font-weight: 700;
    font-size: 24px;
    color: var(--orange);
    letter-spacing: .5px;
  }
  .person__role {
    font-size: 17px;
    color: var(--sky);
    margin-top: 2px;
  }
  .divider {
    position: absolute;
    left: 272px; top: 152px;
    width: 1px; height: 82px;
    background: var(--sky);
    opacity: .6;
  }
  .contacts {
    position: absolute;
    left: 284px; top: 156px;
    list-style: none;
  }
  .contacts li {
    display: flex;
    align-items: center;
    gap: 8px;
    height: 20px;
    font-size: 16px;
    color: var(--white);
  }
  .contacts svg { width: 11px; height: 11px; fill: var(--orange); flex: none; }

  .address-band {
    position: absolute;
    left: 0; top: 256px;
    width: 550px; height: 30px;
    background: var(--orange);
    color: var(--navy);
    font-size: 15px;
    line-height: 30px;
    padding-left: 180px;
  }
  .corner-block {
    position: absolute;
    left: 550px; top: 256px;
    width: 46px; height: 40px;
    background: var(--sky);
  }
</style>
</head>
<body>
  <section class="card card--back" aria-label="Card back">
    <div class="brand">RW HOLLOWAY LLC</div>
  </section>

  <section class="card card--front" aria-label="Card front">
    <div class="person">
      <div class="person__name">DANIEL REYES</div>
      <div class="person__role">President</div>
    </div>
    <div class="divider"></div>
    <ul class="contacts">
      <li><svg viewBox="0 0 12 12"><path d="M2.5 0.5l2 2.2-1 1.3c.7 1.6 2 2.9 3.5 3.5l1.3-1 2.2 2-1.2 2c-4.5-.3-8.3-4.1-8.6-8.6z"/></svg>210-555-0148</li>
      <li><svg viewBox="0 0 12 12"><path d="M3 0h6v12H3zM4 1.5v8h4v-8z"/></svg>210-555-0148</li>
      <li><svg viewBox="0 0 12 12"><path d="M0 2h12v1L6 7 0 3zM0 4.3l6 4 6-4V10H0z"/></svg>reyes@rwholloway.com</li>
      <li><svg viewBox="0 0 12 12"><circle cx="6" cy="6" r="5.5"/></svg>www.rwholloway.com</li>
    </ul>
    <div class="address-band">4120 Cedar Bend Drive, San Antonio, Texas 78230</div>
    <div class="corner-block"></div>
  </section>
</body>
</html>
```